Income Tax Business Cards - Updates

Need to update these business cards while keeping all the same wording but just update them and make them look nicer and more modern/ on brand with our brand.

Industry/Entity Type

finance

Contact Information for Business Card

we have multiple locations so will just need to easily be able to change the address and phone numbers

Colors

Designer to choose colors to be used in the design.

```html
<!DOCTYPE html>
<html lang="en">
<head>
<meta charset="utf-8">
<title>Keystone Tax Group – Business Cards</title>
<link rel="stylesheet" href="https://fonts.googleapis.com/css2?family=Arimo:wght@400;700&family=Tinos:wght@700&display=swap">
<style>
  :root {
    --brand-green: #1d5a32;
    --brand-red: #b01f24;
    --paper: #f7f7f5;
    --ink: #1e1e1e;
    --backdrop: #e4e4e2;
    --white: #ffffff;
  }
  * { margin: 0; padding: 0; box-sizing: border-box; }
  html, body {
    width: 1200px; height: 912px; overflow: hidden;
    background: var(--backdrop);
  }
  .sheet { position: relative; width: 1200px; height: 912px; }
  .card {
    position: absolute; left: 240px; width: 720px; height: 412px;
    overflow: hidden; box-shadow: 0 6px 18px rgba(0,0,0,.18);
  }
  .card--front { top: 30px; background: var(--brand-green); color: var(--white); }
  .card--back  { top: 470px; background: var(--paper); }

  .serif { font-family: "Tinos", "Times New Roman", serif; font-weight: 700; }
  .sans  { font-family: "Arimo", Arial, sans-serif; }

  .brand {
    display: flex; align-items: center; gap: 12px;
    font-family: "Tinos", "Times New Roman", serif; font-weight: 700;
    font-size: 34px; line-height: 1;
  }
  .brand__dot { width: 16px; height: 16px; border-radius: 50%; background: currentColor; flex: none; }

  /* front */
  .front__brand { position: absolute; top: 62px; left: 0; right: 0; justify-content: center; color: var(--white); }
  .front__band {
    position: absolute; top: 148px; left: 0; right: 0; height: 68px;
    background: var(--brand-red);
    display: flex; align-items: center; justify-content: center;
    font-size: 50px; color: var(--white);
  }
  .front__amount {
    position: absolute; top: 238px; left: 0; right: 0; text-align: center;
    font-family: "Arimo", Arial, sans-serif; font-weight: 700; font-size: 78px; line-height: 1;
  }
  .front__advance {
    position: absolute; top: 322px; left: 0; right: 0; text-align: center;
    font-size: 48px; line-height: 1;
  }

  /* back */
  .back__offer { position: absolute; top: 30px; left: 0; width: 560px; text-align: center; }
  .back__amount {
    font-family: "Arimo", Arial, sans-serif; font-weight: 700;
    font-size: 70px; line-height: 1; color: var(--brand-green);
  }
  .back__advance { font-size: 46px; line-height: 1.05; color: var(--brand-red); margin-top: 4px; }
  .back__note { font-size: 24px; line-height: 1.1; color: var(--brand-green); margin-top: 2px; }
  .back__band {
    position: absolute; top: 198px; left: 0; right: 0; height: 60px;
    background: var(--brand-green); color: var(--white);
    display: flex; align-items: center; justify-content: center; font-size: 42px;
  }
  .back__contact {
    position: absolute; top: 274px; left: 64px; color: var(--ink);
    font-size: 21px; line-height: 1.3;
  }
  .contact__phone { display: flex; align-items: center; gap: 8px; font-size: 24px; line-height: 1.2; margin-bottom: 6px; }
  .contact__phone svg { width: 18px; height: 18px; fill: var(--brand-green); }
  .back__brand { position: absolute; top: 296px; right: 46px; color: var(--brand-green); font-size: 30px; }
  .back__rule { position: absolute; left: 0; right: 0; top: 380px; height: 3px; background: var(--brand-red); }
  .back__strip { position: absolute; left: 0; right: 0; top: 388px; bottom: 0; background: var(--brand-green); }
</style>
</head>
<body>
<main class="sheet">
  <section class="card card--front" aria-label="Card front">
    <div class="brand front__brand"><span class="brand__dot"></span>Keystone Tax Group</div>
    <div class="front__band serif">File your Taxes here</div>
    <div class="front__amount">UP to $6000</div>
    <div class="front__advance serif">Same day advance</div>
  </section>

  <section class="card card--back" aria-label="Card back">
    <div class="back__offer">
      <div class="back__amount">UP to $6000</div>
      <div class="back__advance serif">Same day advance</div>
      <div class="back__note sans">on approved tax returns!</div>
    </div>
    <div class="back__band serif">Free Estimates!</div>
    <div class="back__contact sans">
      <div class="contact__phone">
        <svg viewBox="0 0 24 24" aria-hidden="true"><path d="M6.6 10.8a15.1 15.1 0 0 0 6.6 6.6l2.2-2.2a1 1 0 0 1 1-.25 11.4 11.4 0 0 0 3.6.57 1 1 0 0 1 1 1V20a1 1 0 0 1-1 1A17 17 0 0 1 3 4a1 1 0 0 1 1-1h3.5a1 1 0 0 1 1 1c0 1.25.2 2.45.57 3.6a1 1 0 0 1-.25 1z"/></svg>
        (555) 555-0142
      </div>
      <div>2170 Maple Crest Avenue,</div>
      <div>Garden Hill, NY 11020</div>
    </div>
    <div class="brand back__brand"><span class="brand__dot"></span>Keystone Tax Group</div>
    <div class="back__rule"></div>
    <div class="back__strip"></div>
  </section>
</main>
</body>
</html>
```